Wealth management Plorvenet Advertisement

Hello, we are trying to capture more leads to our online booking link through Plorvenet advertisement. We want an attractive modern design to get more clients and catch the attention of high net-worth clients. We deal with high-net-worth retirees, business owners, farmers, and wealth transfer. We offer high-net-worth client solutions that cover Financial Planning, Retirement and Estate Planning, Investment Planning, Tax Planning, and Insurance Planning. The final design that we would be looking for is modern and eye-catching and makes the prospective clients want to click our meeting link to schedule an introductory consultation.

We are in the Wealth Management / Financial Planning industry

Our online booking link Is the following :

https://calendar.brisquelmail.com/owa/calendar/MarcusFenleyPartnersRQPrivateWealth@tovrelfinancial.net/bookings/

Our current Plorvenet page is the following:

https://www.plorvenet.com/FenleyPrivateWealth

Please ask any further questions for needed information for creating design

```html
<!DOCTYPE html>
<html lang="en">
<head>
<meta charset="utf-8">
<title>Protect and Build Your Wealth — Marcus Fenley &amp; Partners</title>
<link href="https://fonts.googleapis.com/css2?family=Montserrat:wght@900&family=Roboto:wght@400;500;700;900&display=swap" rel="stylesheet">
<style>
  :root {
    --navy: #0d2466;
    --blue: #0a74d0;
    --blue-light: #4a9de0;
    --ink: #1f1f1f;
    --band: #e2e3e7;
    --white: #ffffff;
    --photo-warm-a: #e9d3b4;
    --photo-warm-b: #b98a5e;
    --photo-cool-a: #dfe8f2;
    --photo-cool-b: #6f8fb3;
  }
  * { margin: 0; padding: 0; box-sizing: border-box; }
  html, body { width: 1200px; height: 1200px; overflow: hidden; background: var(--white); }
  body { font-family: "Roboto", Arial, sans-serif; color: var(--ink); }
  .ad { position: relative; width: 1200px; height: 1200px; background: var(--white); overflow: hidden; }
  .layer { position: absolute; left: 0; top: 0; }

  .service-band { position: absolute; left: 0; top: 733px; width: 1200px; height: 226px; background: var(--band); }
  .footer { position: absolute; left: 0; top: 958px; width: 1200px; height: 242px; background: var(--navy); }

  .brand { position: absolute; left: 75px; top: 86px; }
  .brand-mark { position: absolute; left: 0; top: 4px; width: 56px; height: 56px; background: var(--navy); }
  .brand-name { position: absolute; left: 89px; top: 0; width: 330px; font-weight: 700; font-size: 25px; line-height: 25px; color: var(--navy); text-transform: uppercase; white-space: nowrap; }
  .brand-team { position: absolute; left: 89px; top: 64px; width: 330px; font-weight: 700; font-size: 25px; line-height: 26px; color: var(--blue); text-transform: uppercase; white-space: nowrap; }

  .headline { position: absolute; left: 66px; top: 236px; color: var(--navy); text-transform: uppercase; white-space: nowrap; }
  .headline-top { font-size: 72px; line-height: 66px; color: var(--ink); font-weight: 900; letter-spacing: -1px; }
  .headline-top .light { font-weight: 400; }
  .headline-mid { font-size: 72px; line-height: 66px; font-weight: 900; letter-spacing: -1px; }
  .headline-big { font-family: "Montserrat", "Arial Black", sans-serif; font-size: 126px; line-height: 104px; font-weight: 900; letter-spacing: -3px; margin-top: 2px; }

  .divider { position: absolute; left: 68px; top: 492px; width: 550px; height: 1px; background: #9a9a9a; }

  .industry { position: absolute; left: 68px; top: 514px; white-space: nowrap; }
  .industry-lead { font-size: 38px; font-weight: 400; line-height: 44px; }
  .industry-strong { font-size: 37px; font-weight: 700; line-height: 46px; }

  .offer-tag { position: absolute; left: 70px; top: 680px; width: 351px; height: 53px; }
  .offer-tag-text { position: absolute; left: 60px; top: 0; font-size: 50px; font-weight: 700; color: var(--white); line-height: 54px; white-space: nowrap; }

  .service { position: absolute; font-size: 23px; font-weight: 500; line-height: 27px; color: var(--ink); white-space: nowrap; }

  .booking-link { position: absolute; left: 74px; top: 991px; width: 600px; font-size: 23px; font-weight: 700; line-height: 30px; color: var(--white); white-space: nowrap; }
  .book-btn { position: absolute; left: 77px; top: 1095px; width: 216px; height: 43px; border-radius: 22px; background: linear-gradient(90deg, #1b8be8, var(--blue)); color: var(--white); font-weight: 700; font-size: 25px; line-height: 43px; padding-left: 56px; white-space: nowrap; }
  .book-btn-icon { position: absolute; left: 4px; top: 4px; }

  .follow { position: absolute; left: 637px; top: 990px; }
  .follow-title { font-size: 36px; font-weight: 700; color: var(--blue); line-height: 42px; }
  .follow-row { display: flex; align-items: center; gap: 9px; margin-top: 12px; font-size: 25px; font-weight: 500; color: var(--white); line-height: 26px; white-space: nowrap; }
  .follow-icon { flex: none; width: 18px; height: 18px; }
</style>
</head>
<body>
<main class="ad">

  <div class="service-band"></div>

  <svg class="layer" width="1200" height="1200" viewBox="0 0 1200 1200">
    <defs>
      <linearGradient id="warmPhoto" x1="0" y1="0" x2="1" y2="1">
        <stop offset="0" stop-color="var(--photo-warm-a)"/>
        <stop offset="0.6" stop-color="#d2ac84"/>
        <stop offset="1" stop-color="var(--photo-warm-b)"/>
      </linearGradient>
      <linearGradient id="coolPhoto" x1="0" y1="0" x2="1" y2="1">
        <stop offset="0" stop-color="#2d4f7e"/>
        <stop offset="0.5" stop-color="var(--photo-cool-a)"/>
        <stop offset="1" stop-color="var(--photo-cool-b)"/>
      </linearGradient>
    </defs>

    <polygon points="644,402 682,364 1012,770 1200,770 1200,832 988,832" fill="var(--blue)"/>
    <polyline points="631,0 512,136 1006,770" fill="none" stroke="var(--navy)" stroke-width="7"/>

    <polygon role="img" aria-label="Photo: a financial advisor meeting with a retired couple at home, reviewing documents"
             points="638,0 1200,0 1200,757 1006,757 524,136" fill="url(#warmPhoto)"/>

    <circle cx="805" cy="602" r="156" fill="var(--blue-light)"/>
    <circle cx="805" cy="602" r="138" fill="var(--white)"/>
    <circle role="img" aria-label="Photo: hands over a desk with charts on a laptop, tablet and papers, plus a calculator"
            cx="805" cy="602" r="131" fill="url(#coolPhoto)"/>

    <polyline points="321,535 618,535 618,648 590,648" fill="none" stroke="#555" stroke-width="1.5"/>

    <g fill="var(--white)" stroke="var(--navy)">
      <g transform="translate(103,803)"><circle r="38" stroke="var(--blue)" stroke-width="1.5"/><circle r="32" stroke-width="6"/></g>
      <g transform="translate(576,803)"><circle r="38" stroke="var(--blue)" stroke-width="1.5"/><circle r="32" stroke-width="6"/></g>
      <g transform="translate(103,896)"><circle r="38" stroke="var(--blue)" stroke-width="1.5"/><circle r="32" stroke-width="6"/></g>
      <g transform="translate(576,896)"><circle r="38" stroke="var(--blue)" stroke-width="1.5"/><circle r="32" stroke-width="6"/></g>
      <g transform="translate(852,896)"><circle r="38" stroke="var(--blue)" stroke-width="1.5"/><circle r="32" stroke-width="6"/></g>
    </g>
    <g fill="none" stroke="#333" stroke-width="1.4" stroke-linecap="round" stroke-linejoin="round">
      <g transform="translate(103,803)">
        <rect x="-13" y="-12" width="18" height="24" rx="1"/><rect x="-8" y="-15" width="8" height="5"/>
        <line x1="-9" y1="-3" x2="1" y2="-3"/><line x1="-9" y1="2" x2="1" y2="2"/><line x1="-9" y1="7" x2="-2" y2="7"/>
        <rect x="2" y="-2" width="12" height="15" rx="1"/><line x1="4" y1="3" x2="12" y2="3"/><line x1="4" y1="8" x2="12" y2="8"/>
        <polyline points="-2,-8 4,-12 8,-9 13,-14"/>
      </g>
      <g transform="translate(576,803)">
        <rect x="-8" y="-15" width="12" height="17"/><line x1="-5" y1="-10" x2="1" y2="-10"/><line x1="-5" y1="-5" x2="1" y2="-5"/>
        <circle cx="9" cy="-11" r="5"/>
        <path d="M-15 6 q6 -4 12 0 h8 q3 0 3 3 l-10 2 M-15 13 l6 -1 h12 l10 -8"/>
      </g>
      <g transform="translate(103,896)">
        <rect x="-12" y="-6" width="14" height="19" rx="1"/><rect x="-9" y="-3" width="8" height="4"/>
        <line x1="-9" y1="5" x2="-1" y2="5"/><line x1="-9" y1="9" x2="-1" y2="9"/>
        <polyline points="-10,-10 -2,-14 4,-10 13,-16"/><polyline points="9,-16 13,-16 13,-12"/>
        <circle cx="9" cy="5" r="4"/><circle cx="9" cy="11" r="4"/>
      </g>
      <g transform="translate(576,896)">
        <path d="M-8 -15 h17 v28 h-20 a3 3 0 0 1 0 -6 h3 z"/>
        <circle cx="-6" cy="4" r="6"/><line x1="1" y1="-2" x2="6" y2="-2"/><line x1="1" y1="3" x2="6" y2="3"/><line x1="1" y1="8" x2="6" y2="8"/>
      </g>
      <g transform="translate(852,896)">
        <path d="M-15 -3 a15 13 0 0 1 30 0 z"/><line x1="0" y1="-16" x2="0" y2="-3"/>
        <circle cx="-4" cy="8" r="5"/><circle cx="6" cy="9" r="6"/>
      </g>
    </g>

    <polygon points="70,680 421,680 398,733 70,733" fill="var(--blue)"/>
  </svg>

  <div class="brand">
    <div class="brand-mark"></div>
    <div class="brand-name">RQ Private Wealth<br>Management</div>
    <div class="brand-team">Marcus Fenley<br>&amp; Partners</div>
  </div>

  <h1 class="headline">
    <div class="headline-top">Protect <span class="light">and</span></div>
    <div class="headline-mid">Build your</div>
    <div class="headline-big">Wealth</div>
  </h1>

  <div class="divider"></div>

  <div class="industry">
    <div class="industry-lead">We are in the</div>
    <div class="industry-strong">Wealth Management</div>
    <div class="industry-strong">Financial Planning industry</div>
  </div>

  <div class="offer-tag"><div class="offer-tag-text">WE OFFER</div></div>

  <div class="service" style="left:159px; top:776px;">High-net-worth client solutions<br>that cover Financial Planning</div>
  <div class="service" style="left:630px; top:776px;">Retirement and<br>Estate Planning</div>
  <div class="service" style="left:159px; top:884px;">Investment Planning</div>
  <div class="service" style="left:630px; top:880px;">Tax Planning</div>
  <div class="service" style="left:903px; top:880px;">Insurance Planning</div>

  <footer class="footer"></footer>

  <div class="booking-link">https://calendar.brisquelmail.com/owa/calendar/<br>MarcusFenleyPartnersRQPrivate<br>Wealth@tovrelfinancial.net/bookings/</div>

  <div class="book-btn">
    <svg class="book-btn-icon" width="35" height="35" viewBox="0 0 35 35" aria-hidden="true">
      <circle cx="17.5" cy="17.5" r="17.5" fill="var(--white)"/>
      <path d="M15 9 v12 l-3 -3 l-2 2 l6 7 h7 l2 -7 v-4 h-4 v-1 h-3 v-6 z" fill="none" stroke="var(--navy)" stroke-width="1.5" stroke-linejoin="round"/>
    </svg>
    BOOK NOW
  </div>

  <div class="follow">
    <div class="follow-title">follow us</div>
    <div class="follow-row">
      <svg class="follow-icon" viewBox="0 0 18 18" aria-hidden="true"><rect width="18" height="18" rx="2" fill="var(--blue)"/></svg>
      www.plorvenet.com/FenleyPrivateWealth
    </div>
    <div class="follow-row">
      <svg class="follow-icon" viewBox="0 0 18 18" aria-hidden="true" fill="none" stroke="var(--blue)" stroke-width="1.4">
        <circle cx="9" cy="9" r="8"/><ellipse cx="9" cy="9" rx="3.5" ry="8"/><line x1="1" y1="9" x2="17" y2="9"/><line x1="2.5" y1="5" x2="15.5" y2="5"/><line x1="2.5" y1="13" x2="15.5" y2="13"/>
      </svg>
      www.marcusfenleyandpartners.ca
    </div>
  </div>

</main>
</body>
</html>
```